verdant terraces simple classy business card design

my name is colin barrow and I run a gardening business aimed at high class verdant terraces. the business name is verdant terraces and our logo was designed on pixel harbour .My clientel are anything from residential homes to businesses. I take pride in my work and know that I offer a service like no other in my area.
The business card will be used to represent my business and I want it to be not only rememberable, but simplistic and modern. Eye catching too. Of course I would like it relatable to gardening and appealing to the correct clientel - those being garden enthusiasts, prestigious homes and businesses that are after top of the line gardening services like no other on the market.
I am not a typical lawn mowing business so I don't want a typical card design that represents that. The gardens I work with are generally million dollar properties with owners who are very garden proud looking for upkeep and guidance from me along with sometimes whole new garden designs. I want the business cards to show to my clients that I take pride, as they do, in their garden. And I want them to know from my card that I am a professional, qualified horticulturist offering them a top of the line service for life. I want them to refer my business on. I want them to look at my business card and see class and professionalism in a modern unique bold way.
The card should be simple with the possibility of the logo on the front being embossed/debossed and my details on the back the card should have a organic garden feel it's very important to me that it is absolutely perfect
I am also very open to ideas and suggestions so look forward to seeing the designs. the business logo has been supplied with this project and I want the card to be double sided

Contact info is
Colin Barrow - Managing Director / Horticulturist
Phone : 0481 526 704
Email: colinbarrow@verdantterraces.example.au

Target Market(s)

high class gardens residential and commercial

Industry/Entity Type

Gardener

Contact Information for Business Card

Contact info is
Phone : 0481 526 704

PLEASE MAKE CARD DOUBLE SIDED

Requirements
Must have
• organic simple classy modern feel
• must flow with the current logo that has been supplied with this project
• Double sided
• Must explain in a simple way that I deal with high end gardens and I'm a qualified horticulturist
Nice to have
• embossed debossed logo
Should not have
• shouldn't be to busy or cheap looking

```html
<!DOCTYPE html>
<html lang="en">
<head>
<meta charset="utf-8">
<title>Verdant Terraces — Business Card</title>
<link href="https://fonts.googleapis.com/css2?family=Montserrat:wght@300;400;500&display=swap" rel="stylesheet">
<style>
  :root {
    --page-bg: #e6e7e9;
    --leaf-green: #5f9e5c;
    --deep-green: #4f8a4c;
    --card-white: #ffffff;
    --ink-light: #ffffff;
  }
  html, body {
    margin: 0;
    padding: 0;
    width: 1200px;
    height: 910px;
    overflow: hidden;
    background: var(--page-bg);
    font-family: "Montserrat", Arial, sans-serif;
  }
  .canvas {
    position: relative;
    width: 1200px;
    height: 910px;
  }
  .card {
    position: absolute;
    top: 80px;
    width: 428px;
    height: 750px;
    border-radius: 32px;
    box-sizing: border-box;
  }
  .card--front {
    left: 165px;
    background: var(--leaf-green);
    color: var(--ink-light);
    text-align: center;
  }
  .card--back {
    left: 630px;
    background: var(--card-white);
  }
  .brand-mark {
    position: absolute;
    left: 0;
    right: 0;
    top: 345px;
    margin: 0;
    font-weight: 400;
    font-size: 29px;
    letter-spacing: 3px;
    text-transform: uppercase;
    color: var(--deep-green);
  }
  .contact-name {
    position: absolute;
    left: 0;
    right: 0;
    top: 418px;
    margin: 0;
    font-weight: 500;
    font-size: 30px;
    letter-spacing: 0.3px;
  }
  .contact-role {
    position: absolute;
    left: 0;
    right: 0;
    top: 456px;
    margin: 0;
    font-weight: 300;
    font-size: 17.5px;
    letter-spacing: 0.6px;
  }
  .contact-icons {
    position: absolute;
    left: 0;
    right: 0;
    top: 488px;
    display: flex;
    justify-content: center;
    gap: 6px;
  }
  .contact-line {
    position: absolute;
    left: 0;
    right: 0;
    margin: 0;
    font-weight: 300;
    font-size: 17.5px;
    letter-spacing: 0.4px;
  }
  .contact-phone { top: 511px; }
  .contact-email { top: 535px; }
  .back-circle {
    position: absolute;
    left: 114px;
    top: 210px;
    width: 200px;
    height: 200px;
    border-radius: 50%;
    background: var(--leaf-green);
  }
  .back-brand {
    position: absolute;
    left: 0;
    right: 0;
    top: 440px;
    margin: 0;
    text-align: center;
    font-weight: 400;
    font-size: 24px;
    letter-spacing: 3px;
    text-transform: uppercase;
    color: var(--leaf-green);
  }
</style>
</head>
<body>
<main class="canvas">
  <section class="card card--front" aria-label="Card front">
    <p class="brand-mark">Verdant Terraces</p>
    <h1 class="contact-name">Colin Barrow</h1>
    <p class="contact-role">Managing Director / Horticulturist</p>
    <div class="contact-icons" aria-hidden="true">
      <svg width="11" height="12" viewBox="0 0 11 12">
        <path d="M2.5 1 L4.3 3.4 L3.3 4.6 C3.9 6.3 5 7.6 6.6 8.5 L7.8 7.5 L10 9.3 L8.6 11 C4.5 10.2 1.3 6.7 1 2.3 Z" fill="none" stroke="#fff" stroke-width="1.1" stroke-linejoin="round"/>
      </svg>
      <svg width="13" height="12" viewBox="0 0 13 12">
        <rect x="1" y="2.5" width="11" height="7.5" fill="none" stroke="#fff" stroke-width="1.1"/>
        <path d="M1 2.5 L6.5 7 L12 2.5" fill="none" stroke="#fff" stroke-width="1.1"/>
      </svg>
    </div>
    <p class="contact-line contact-phone">0481 526 704</p>
    <p class="contact-line contact-email">colinbarrow@verdantterraces.example.au</p>
  </section>

  <section class="card card--back" aria-label="Card back">
    <div class="back-circle" aria-hidden="true"></div>
    <p class="back-brand">Verdant Terraces</p>
  </section>
</main>
</body>
</html>
```